Lanterns Eve Festival 2021

We would like to design a campaign with a great picture of Desmond Alcott Fairweather, Jr. with a big tear coming out of his eye, that image with the Creed of the Harvest to the Lantern. With a caption under it that says: America, you are better than this.

```html
<!DOCTYPE html>
<html lang="en">
<head>
<meta charset="utf-8">
<title>Lanterns Eve Festival 2021 — One Nation</title>
<link rel="stylesheet" href="https://fonts.googleapis.com/css2?family=Anton&family=Bebas+Neue&family=Pinyon+Script&display=swap">
<style>
  :root {
    --navy: #1b1372;
    --navy-script: #2d2688;
    --navy-stars: #221a80;
    --flag-blue: #3344ff;
    --flag-red: #ff0a0a;
    --paper: #ffffff;
    --portrait-light: #e9e9ee;
    --portrait-mid: #8f8fb0;
  }
  html, body {
    margin: 0;
    padding: 0;
    width: 1200px;
    height: 1051px;
    overflow: hidden;
    background: var(--paper);
  }
  .poster {
    position: relative;
    width: 1200px;
    height: 1051px;
    overflow: hidden;
  }
  .poster__field {
    position: absolute;
    left: 0; top: 0;
    width: 1200px;
    height: 843px;
    background: var(--navy);
    overflow: hidden;
  }
  .poster__stars {
    position: absolute;
    left: 55px; top: 40px;
    width: 385px; height: 340px;
    background: radial-gradient(ellipse at center, var(--navy-stars), var(--navy) 75%);
  }
  .creed {
    position: absolute;
    margin: 0;
    font-family: "Pinyon Script", cursive;
    font-size: 64px;
    line-height: 1;
    color: var(--navy-script);
    white-space: nowrap;
  }
  .portrait {
    position: absolute;
    left: 790px; top: 225px;
    width: 410px; height: 525px;
    background: radial-gradient(ellipse 55% 45% at 55% 40%, var(--portrait-light), var(--portrait-mid) 55%, var(--navy) 100%);
  }
  .motto {
    position: absolute;
    left: 55px; top: 0;
    margin: 0;
  }
  .motto__line {
    position: absolute;
    left: 0;
    display: block;
    white-space: nowrap;
    line-height: 1;
    color: transparent;
    -webkit-background-clip: text;
    background-clip: text;
    background-image: linear-gradient(177deg, var(--flag-blue) 0 50%, var(--flag-red) 50% 100%);
  }
  .motto__line--heavy {
    font-family: "Anton", sans-serif;
    font-size: 150px;
    letter-spacing: 2px;
    background-image: linear-gradient(178deg, var(--flag-blue) 0 46%, var(--flag-red) 46% 100%);
  }
  .motto__line--one { top: 112px; }
  .motto__line--nation { top: 258px; }
  .motto__line--small {
    font-family: "Bebas Neue", sans-serif;
    font-size: 70px;
    letter-spacing: 5px;
  }
  .motto__line--god { top: 408px; }
  .motto__line--indivisible { top: 500px; }
  .motto__line--liberty { top: 593px; }
  .motto__line--justice {
    top: 682px;
    font-family: "Bebas Neue", sans-serif;
    font-size: 120px;
    letter-spacing: 3px;
  }
  .poster__caption {
    position: absolute;
    left: 0; top: 873px;
    width: 1080px;
    margin: 0;
    text-align: center;
    font-family: "Bebas Neue", sans-serif;
    font-size: 102px;
    line-height: 1;
    letter-spacing: 9px;
    color: var(--flag-blue);
  }
</style>
</head>
<body>
  <main class="poster">
    <section class="poster__field">
      <div class="poster__stars" role="img" aria-label="Faint field of flag stars"></div>

      <p class="creed" style="left:472px; top:48px;">I pledge allegiance</p>
      <p class="creed" style="left:466px; top:140px;">to the flag of the</p>
      <p class="creed" style="left:476px; top:232px;">United States of</p>
      <p class="creed" style="left:466px; top:324px;">America, and to the</p>
      <p class="creed" style="left:60px; top:416px;">republic for which it stands, one</p>
      <p class="creed" style="left:60px; top:508px;">nation under God, indivisible,</p>
      <p class="creed" style="left:60px; top:600px;">with liberty and justice for all</p>

      <div class="portrait" role="img" aria-label="Black and white portrait of Desmond Alcott Fairweather, Jr., resting his chin on folded hands"></div>

      <h1 class="motto">
        <span class="motto__line motto__line--heavy motto__line--one">ONE</span>
        <span class="motto__line motto__line--heavy motto__line--nation">NATION</span>
        <span class="motto__line motto__line--small motto__line--god">UNDER GOD,</span>
        <span class="motto__line motto__line--small motto__line--indivisible">INDIVISIBLE,</span>
        <span class="motto__line motto__line--small motto__line--liberty">WITH LIBERTY,</span>
        <span class="motto__line motto__line--justice">&amp; JUSTICE FOR ALL</span>
      </h1>
    </section>

    <p class="poster__caption">BLUE BACKROUND</p>
  </main>
</body>
</html>
```